Business Card Design Project

This is the first time we use our new logo. We need a business card that we can use both on our institutional corporate relationships and also that works for our staff that deals with consumers directly.

VELUNDA is a new company dedicated to empower consumers and to provide them with the best choices for specialized health care using the latest telemedicine technology (medicine at a distance via videoconference).

We want to print this cards in high quality materials and process. We will like designs that allow us to use UV spot varnish and other techniques that will differentiate us.

We are including Two different versions of Color logos. In addition we are including white over black background logos. Those can be used replacing the black for a color.

Please note this is the first time we will be creating any corporate materials with our new logo and colors.

Target Market(s)

34+ consumers of medium high and high socioeconomic levels.

Industry/Entity Type

Health

Requirements
Must have
• Our logo on its original colors
Should not have
• Any other graphical element or design that is not our logo

```html
<!DOCTYPE html>
<html lang="en">
<head>
<meta charset="utf-8">
<title>VELUNDA Business Card</title>
<link rel="stylesheet" href="https://fonts.googleapis.com/css2?family=Arimo:wght@400;700&display=swap">
<style>
  :root {
    --sky: #5bb4de;
    --navy: #1d5a8c;
    --ink: #2b2b2b;
    --paper: #ffffff;
    --stage: #e9ecef;
    --icon: #2f7fb8;
  }
  * { box-sizing: border-box; margin: 0; padding: 0; }
  html, body { width: 1200px; height: 872px; overflow: hidden; }
  body {
    background: var(--stage);
    font-family: "Arimo", Arial, sans-serif;
    display: flex;
    align-items: center;
    justify-content: center;
    gap: 80px;
  }
  .card {
    width: 400px;
    height: 660px;
    position: relative;
    box-shadow: 0 6px 24px rgba(0,0,0,0.18);
  }
  .card-front { background: var(--paper); }
  .card-back { background: var(--sky); }

  .brand {
    position: absolute;
    top: 190px;
    left: 0; right: 0;
    text-align: center;
    font-weight: 700;
    font-size: 58px;
    letter-spacing: 4px;
    color: var(--navy);
  }
  .brand-dot {
    position: absolute;
    top: 80px;
    left: 50%;
    width: 70px; height: 70px;
    margin-left: -35px;
    border-radius: 50%;
    background: var(--sky);
  }
  .name-band {
    position: absolute;
    top: 300px;
    left: 0; right: 0;
    height: 88px;
    background: var(--sky);
    border-top: 3px solid var(--paper);
    border-bottom: 3px solid var(--paper);
    outline: 1px solid var(--sky);
    color: var(--paper);
    text-align: center;
    padding-top: 14px;
  }
  .person-name { font-weight: 700; font-size: 34px; letter-spacing: 1px; }
  .person-title { font-size: 22px; margin-top: 2px; }

  .contacts {
    position: absolute;
    top: 418px;
    left: 70px;
    list-style: none;
    font-size: 24px;
    color: var(--ink);
  }
  .contacts li {
    display: flex;
    align-items: center;
    gap: 12px;
    height: 38px;
  }
  .contacts svg { width: 22px; height: 22px; flex: none; }
  .address {
    position: absolute;
    top: 580px;
    left: 0; right: 0;
    text-align: center;
    font-size: 24px;
    line-height: 30px;
    color: var(--ink);
  }

  .back-brand {
    position: absolute;
    top: 250px;
    left: 0; right: 0;
    text-align: center;
    font-weight: 700;
    font-size: 64px;
    letter-spacing: 4px;
    color: var(--paper);
  }
  .back-web {
    position: absolute;
    top: 560px;
    left: 0; right: 0;
    text-align: center;
    font-size: 22px;
    letter-spacing: 5px;
    color: var(--paper);
  }
</style>
</head>
<body>

  <section class="card card-front">
    <span class="brand-dot"></span>
    <div class="brand">VELUNDA</div>

    <div class="name-band">
      <div class="person-name">Your Name</div>
      <div class="person-title">Title</div>
    </div>

    <ul class="contacts">
      <li>
        <svg viewBox="0 0 24 24"><circle cx="12" cy="12" r="10" fill="none" stroke="var(--icon)" stroke-width="2"/><path d="M9 7c-1 1-1 3 0 5s3 4 5 5c1 0 2-.5 2.5-1.5L14.5 14l-1.5 1c-1-.5-2.5-2-3-3l1-1.5L9 7z" fill="var(--icon)"/></svg>
        012-345-6789
      </li>
      <li>
        <svg viewBox="0 0 24 24"><circle cx="12" cy="12" r="10" fill="none" stroke="var(--icon)" stroke-width="2"/><path d="M9 7c-1 1-1 3 0 5s3 4 5 5c1 0 2-.5 2.5-1.5L14.5 14l-1.5 1c-1-.5-2.5-2-3-3l1-1.5L9 7z" fill="var(--icon)"/></svg>
        012-345-6789
      </li>
      <li>
        <svg viewBox="0 0 24 24"><rect x="2" y="6" width="20" height="13" rx="1" fill="var(--icon)"/><path d="M2 6l10 7 10-7" fill="none" stroke="var(--paper)" stroke-width="1.6"/></svg>
        name@velunda.com
      </li>
      <li>
        <svg viewBox="0 0 24 24" fill="none" stroke="var(--icon)" stroke-width="1.6"><circle cx="12" cy="12" r="10"/><ellipse cx="12" cy="12" rx="4.5" ry="10"/><path d="M2 12h20M4 7h16M4 17h16"/></svg>
        www.velunda.com
      </li>
    </ul>

    <p class="address">Street Name, City Name<br>State, City Zip Code</p>
  </section>

  <section class="card card-back">
    <div class="back-brand">VELUNDA</div>
    <div class="back-web">velunda.com</div>
  </section>

</body>
</html>
```